Business card for Bio pharmaceutical company

Hello,
We are a bio pharmaceutical contract manufacturing company in Brisbane, Australia. Can you please create a new business card design. Please go to our website for colours http://www.corvalinbio.com.au.
On the back can you include the cartoon mascot Tobi Tumlo and the tagline
"A Global Biopharmaceutical Contract Development Manufacturing Company"
Target Market(s)
Biotechnology
Industry/Entity Type
Pharmaceutical
Contact Information for Business Card
Maren Holtby
Business Development Manager
maren.holtby@corvalinbio.com.au
1947 Kestrel Road Marlow Queesnland 4183 Australia
T: +61 7 3951 4820
M +61 415 206 718
F +61 7 3842 6093
www.corvalinbio.com.au

```html
<!DOCTYPE html>
<html lang="en">
<head>
<meta charset="utf-8">
<title>Corvalin Bio – Business Card</title>
<link href="https://fonts.googleapis.com/css2?family=Exo+2:wght@400;500;700&display=swap" rel="stylesheet">
<style>
  :root {
    --navy: #0b4f71;
    --lime: #c2d44b;
    --paper: #f3f4f3;
    --paper-shade: #e6e8e7;
    --white: #ffffff;
    --backdrop: #dfe1e8;
  }
  * { box-sizing: border-box; margin: 0; padding: 0; }
  html, body {
    width: 1200px;
    height: 840px;
    overflow: hidden;
    background: var(--backdrop);
    font-family: "Exo 2", sans-serif;
  }
  .card {
    position: absolute;
    left: 100px;
    top: 135px;
    width: 1000px;
    height: 570px;
    background: linear-gradient(160deg, var(--white), var(--paper) 50%, var(--paper-shade));
    overflow: hidden;
    box-shadow: 0 10px 30px rgba(20, 30, 60, 0.18);
  }
  .card-shapes {
    position: absolute;
    inset: 0;
    width: 100%;
    height: 100%;
  }
  .brand {
    position: absolute;
    left: 70px;
    top: 250px;
    display: flex;
    align-items: flex-start;
    gap: 14px;
  }
  .brand-name {
    font-weight: 700;
    font-size: 76px;
    letter-spacing: -0.5px;
    color: var(--navy);
    line-height: 1;
  }
  .brand-dot {
    width: 26px;
    height: 26px;
    border-radius: 50%;
    background: var(--lime);
    margin-top: -12px;
  }
  .holder {
    position: absolute;
    right: 42px;
    top: 52px;
    text-align: right;
    color: var(--white);
    text-transform: uppercase;
  }
  .holder-name {
    font-weight: 500;
    font-size: 26px;
    letter-spacing: 1.5px;
  }
  .holder-title {
    font-size: 17px;
    letter-spacing: 1.5px;
    margin-top: 2px;
  }
  .address {
    position: absolute;
    right: 42px;
    top: 172px;
    text-align: right;
    color: var(--white);
    font-size: 20px;
    line-height: 1.4;
    letter-spacing: 0.5px;
  }
  .contacts {
    position: absolute;
    right: 42px;
    top: 290px;
    list-style: none;
    color: var(--white);
    font-size: 19px;
    letter-spacing: 0.8px;
  }
  .contact-line {
    display: flex;
    justify-content: flex-end;
    align-items: center;
    gap: 12px;
    height: 40px;
  }
  .contact-icon {
    width: 20px;
    height: 20px;
    flex: none;
  }
  .contact-line--plain { padding-right: 32px; }
</style>
</head>
<body>
  <div class="card">
    <svg class="card-shapes" viewBox="0 0 1000 570" preserveAspectRatio="none" aria-hidden="true">
      <path fill="var(--lime)" d="M765,0 C690,250 420,455 0,458 L0,570 L1000,570 L1000,0 Z"/>
      <path fill="var(--navy)" d="M782,0 C705,265 430,472 0,474 L0,570 L1000,570 L1000,0 Z"/>
    </svg>

    <div class="brand">
      <span class="brand-name">Corvalin Bio</span>
      <span class="brand-dot"></span>
    </div>

    <div class="holder">
      <p class="holder-name">Maren Holtby</p>
      <p class="holder-title">President</p>
    </div>

    <p class="address">041,12th floor,Mall<br>Kestrel Road MLW</p>

    <ul class="contacts">
      <li class="contact-line">
        <span>012 345 6789</span>
        <svg class="contact-icon" viewBox="0 0 24 24" aria-label="Telephone"><path fill="var(--white)" d="M6.6 10.8a15 15 0 0 0 6.6 6.6l2.2-2.2c.3-.3.7-.4 1-.2 1.1.4 2.3.6 3.6.6.6 0 1 .4 1 1V20c0 .6-.4 1-1 1A17 17 0 0 1 3 4c0-.6.4-1 1-1h3.5c.6 0 1 .4 1 1 0 1.3.2 2.5.6 3.6.1.3 0 .7-.2 1z"/></svg>
      </li>
      <li class="contact-line">
        <span>012 345 6789</span>
        <svg class="contact-icon" viewBox="0 0 24 24" aria-label="Mobile"><rect x="6" y="2" width="12" height="20" rx="2" fill="none" stroke="var(--white)" stroke-width="2"/><circle cx="12" cy="18" r="1.2" fill="var(--white)"/></svg>
      </li>
      <li class="contact-line">
        <span>012 345 6789</span>
        <svg class="contact-icon" viewBox="0 0 24 24" aria-label="Fax"><rect x="3" y="9" width="18" height="12" rx="1.5" fill="var(--white)"/><rect x="7" y="3" width="10" height="7" fill="none" stroke="var(--white)" stroke-width="2"/><rect x="6" y="13" width="12" height="1.6" fill="var(--navy)"/><rect x="6" y="16.5" width="8" height="1.6" fill="var(--navy)"/></svg>
      </li>
      <li class="contact-line">
        <span>urname@email.com</span>
        <svg class="contact-icon" viewBox="0 0 24 24" aria-label="Email"><rect x="2" y="5" width="20" height="14" rx="1.5" fill="var(--white)"/><path d="M2.5 6 L12 13 L21.5 6" fill="none" stroke="var(--navy)" stroke-width="1.8"/></svg>
      </li>
      <li class="contact-line">
        <span>www.urwebsitename.com</span>
        <svg class="contact-icon" viewBox="0 0 24 24" aria-label="Website"><g fill="none" stroke="var(--white)" stroke-width="1.8"><circle cx="12" cy="12" r="9.5"/><ellipse cx="12" cy="12" rx="4.2" ry="9.5"/><path d="M2.5 12h19M4 7h16M4 17h16"/></g></svg>
      </li>
    </ul>
  </div>
</body>
</html>
```